Awesome photographers card for an awesome new business

Double sided business card Black background and silver logo in middle on one side. Details on otherside. please keep it simple

Industry/Entity Type

Photographer

Contact Information for Business Card

Gerald Fenwick
0452817360
GeraldFenwickPhotography47@mailbox.test
www.GeraldFenwickPhotography.test.au
Instagram _Gerald_fenwick

Requirements
Must have
• My logo in Silver
• please use instagram logo instead of "Instagram"

```html
<!DOCTYPE html>
<html lang="en">
<head>
<meta charset="utf-8">
<title>Gerald Fenwick Photography – Business Card</title>
<link rel="stylesheet" href="https://fonts.googleapis.com/css2?family=Mulish:wght@400;600;700&display=swap">
<style>
  :root {
    --backdrop: #d6d6d6;
    --card-white: #f4f4f4;
    --silver-light: #d9d9d9;
    --silver-mid: #a8a8a8;
    --silver-dark: #6f6f6f;
    --card-black: #151515;
    --text-white: #ffffff;
    --logo-silver: #b9b9b9;
  }
  * { margin: 0; padding: 0; box-sizing: border-box; }
  html, body {
    width: 1200px; height: 960px; overflow: hidden;
    background: var(--backdrop);
    font-family: "Mulish", "Helvetica Neue", Arial, sans-serif;
  }
  .canvas { position: relative; width: 1200px; height: 960px; }
  .card {
    position: absolute; width: 600px; height: 342px;
    border-radius: 16px; overflow: hidden;
    box-shadow: 0 3px 6px rgba(0,0,0,0.25);
  }
  .card-front { left: 322px; top: 126px; background: var(--card-white); }
  .card-back { left: 320px; top: 501px; background: var(--card-black); }
  .front-swoosh { position: absolute; inset: 0; }
  .brand-mark {
    position: absolute; display: flex; align-items: center; justify-content: center;
    border-radius: 50%; border: 4px solid var(--logo-silver);
  }
  .brand-mark .brand-name {
    font-weight: 600; color: var(--logo-silver); letter-spacing: 2px;
    text-transform: uppercase; text-align: center; line-height: 1.3;
  }
  .card-front .brand-mark { left: 56px; top: 70px; width: 164px; height: 164px; }
  .card-front .brand-name { font-size: 15px; }
  .back-pattern { position: absolute; inset: 0; background: var(--card-black); }
  .card-back .brand-mark { left: 195px; top: 66px; width: 210px; height: 210px; }
  .card-back .brand-name { font-size: 20px; }
  .contact {
    position: absolute; right: 32px; top: 206px;
    color: var(--text-white); text-align: right;
  }
  .contact .person-name {
    font-size: 18px; font-weight: 700; text-transform: uppercase;
    letter-spacing: 0.3px; margin-bottom: 8px;
  }
  .contact .line {
    display: flex; justify-content: flex-end; align-items: center;
    font-size: 13px; height: 18.5px; gap: 10px;
  }
  .contact .icon { width: 12px; height: 12px; flex: none; }
  .contact .plain-square { width: 11px; height: 11px; background: var(--text-white); border-radius: 2px; flex: none; }
</style>
</head>
<body>
<main class="canvas">
  <section class="card card-front">
    <svg class="front-swoosh" viewBox="0 0 600 342" width="600" height="342">
      <defs>
        <linearGradient id="swooshFill" x1="0" y1="1" x2="1" y2="0">
          <stop offset="0" stop-color="var(--silver-light)"/>
          <stop offset="0.5" stop-color="var(--silver-mid)"/>
          <stop offset="1" stop-color="var(--silver-dark)"/>
        </linearGradient>
      </defs>
      <path d="M0,342 L0,336 C160,330 260,230 360,130 C430,62 510,22 600,12 L600,342 Z" fill="#c8c8c8"/>
      <path d="M0,342 C170,338 270,240 370,140 C440,72 520,30 600,22 L600,342 Z" fill="url(#swooshFill)"/>
    </svg>
    <div class="brand-mark"><span class="brand-name">Gerald<br>Fenwick</span></div>
    <div class="contact">
      <p class="person-name">Gerald Fenwick</p>
      <p class="line">0452817360
        <svg class="icon" viewBox="0 0 24 24"><path fill="#fff" d="M6.6 10.8a15.1 15.1 0 0 0 6.6 6.6l2.2-2.2c.3-.3.7-.4 1-.2 1.1.4 2.3.6 3.6.6.6 0 1 .4 1 1V20c0 .6-.4 1-1 1A17 17 0 0 1 3 4c0-.6.4-1 1-1h3.5c.6 0 1 .4 1 1 0 1.3.2 2.5.6 3.6.1.3 0 .7-.2 1z"/></svg></p>
      <p class="line">GeraldFenwickPhotography47@mailbox.test
        <svg class="icon" viewBox="0 0 24 24"><path fill="#fff" d="M2 5h20v14H2z"/><path fill="none" stroke="#888" stroke-width="2" d="M2 5l10 8 10-8"/></svg></p>
      <p class="line">www.GeraldFenwickPhotography.test.au
        <svg class="icon" viewBox="0 0 24 24"><circle cx="12" cy="12" r="10" fill="none" stroke="#fff" stroke-width="2"/><path fill="none" stroke="#fff" stroke-width="2" d="M2 12h20M12 2c3 3 3 17 0 20M12 2c-3 3-3 17 0 20"/></svg></p>
      <p class="line">Gerald_fenwick <span class="plain-square"></span></p>
    </div>
  </section>

  <section class="card card-back">
    <div class="back-pattern" role="img" aria-label="Faint repeated monogram pattern on black"></div>
    <div class="brand-mark"><span class="brand-name">Gerald<br>Fenwick</span></div>
  </section>
</main>
</body>
</html>
```